I need a 6 x 11 postcard created that adheres to the design templates of the Federated parcel bureau. It will be mailed to scholars to encourage them to attend and present papers at the Marrowgate Indie International Film Festival's "Frame, Signal, and Score Conference." It must be provocative and engaging like a film festival poster. One option would be to high light the glitz of Hollywood and the appeal of the beach/shoreline in Long Beach but that's just one idea and I would love for the designer to just come with something original. It should be artistically compelling in that it would cause someone to keep the postcard even if they didn't care about the event. It must stand out in the mail and on a bulletin board.

You DO NOT have to use logo that I included and you do not have to stick with color schemes that are on logo.

My notes are in red on the document that includes the text.

the front can be portrait or landscape but back must be landscape. Also, designs submitted should include front and back.

You do not have to use the logo I included. If you do use the logo you can change the colors to fit your design Ideas.

The postcard will be sent to scholars who study and write about film, television, music, and digital media. We are inviting them to participate in a conference by selling them hollywood and the beaches of southern california.

Festival

• The design must be bold and inventive. Either ultramodern or just artistically appealing. The words 'Frame, Signal, and Score Conference" and "Call for Papers, Films, and Exhibitors Now Open!" must be clear on the front. It should be bright and inviting or classically beautiful (e.g. black and white).

It must match the Federated Parcel Bureau design requirements for 6 x 11 postcards
• This has got to be taken seriously by some very creative and intelligent people who love art, film, etc.

```html
<!DOCTYPE html>
<html lang="en">
<head>
<meta charset="utf-8">
<title>Frame, Signal, and Score Conference — Postcard</title>
<link rel="stylesheet" href="https://fonts.googleapis.com/css2?family=Raleway:wght@200;300&display=swap">
<style>
  :root {
    --backdrop: #e8e8e8;
    --card-white: #f7f7f7;
    --rule: #8a8a8a;
    --disc: #262c2e;
    --ink-light: #f2f4f4;
    --sea-violet: #6f6a88;
    --sea-teal: #8fb9bf;
    --sea-foam: #d3e4e6;
    --sea-deep: #3a4547;
  }
  * { margin: 0; padding: 0; box-sizing: border-box; }
  html, body { width: 1200px; height: 924px; overflow: hidden; }
  body {
    background: var(--backdrop);
    font-family: "Raleway", sans-serif;
    display: flex;
    flex-direction: column;
    align-items: center;
    justify-content: center;
    gap: 24px;
  }
  .postcard {
    position: relative;
    width: 800px;
    height: 436px;
    box-shadow: 0 2px 6px rgba(0,0,0,0.12);
  }
  /* Address side */
  .postcard-back { background: var(--card-white); }
  .postcard-back svg { position: absolute; inset: 0; }
  /* Picture side */
  .postcard-front { overflow: hidden; }
  .shoreline-photo {
    position: absolute;
    inset: 0;
    background:
      radial-gradient(ellipse 55% 35% at 30% 62%, var(--sea-foam) 0%, rgba(211,228,230,0) 70%),
      radial-gradient(ellipse 50% 60% at 85% 70%, var(--sea-deep) 0%, rgba(58,69,71,0) 75%),
      linear-gradient(160deg, var(--sea-violet) 0%, #7b7592 25%, var(--sea-teal) 50%, #6f9aa0 70%, var(--sea-deep) 100%);
  }
  .front-graphics { position: absolute; inset: 0; }
  .disc { fill: var(--disc); opacity: 0.9; }
  .title-text { fill: var(--ink-light); font-family: "Raleway", sans-serif; font-weight: 200; text-transform: uppercase; }
  .detail-text { fill: var(--ink-light); font-family: "Raleway", sans-serif; font-weight: 300; text-transform: uppercase; }
</style>
</head>
<body>

  <section class="postcard postcard-back" aria-label="Postcard address side">
    <svg width="800" height="436" viewBox="0 0 800 436">
      <line class="divider" x1="420" y1="40" x2="420" y2="396" stroke="var(--rule)" stroke-width="1.2"/>
      <rect class="stamp-box" x="700" y="28" width="52" height="60" fill="none" stroke="var(--rule)" stroke-width="1.2"/>
      <g class="address-lines" stroke="var(--rule)" stroke-width="1">
        <line x1="470" y1="250" x2="740" y2="250"/>
        <line x1="470" y1="280" x2="740" y2="280"/>
        <line x1="470" y1="310" x2="740" y2="310"/>
        <line x1="470" y1="340" x2="740" y2="340"/>
      </g>
    </svg>
  </section>

  <section class="postcard postcard-front" aria-label="Postcard picture side">
    <div class="shoreline-photo" role="img" aria-label="Photograph of waves breaking on a shoreline, toned in violet, teal and slate"></div>
    <svg class="front-graphics" width="800" height="436" viewBox="0 0 800 436">
      <circle class="disc" cx="400" cy="190" r="118"/>
      <circle class="disc" cx="232" cy="205" r="64"/>
      <circle class="disc" cx="598" cy="238" r="62"/>
      <circle class="disc" cx="644" cy="46" r="30"/>
      <circle class="disc" cx="512" cy="128" r="40"/>
      <circle class="disc" cx="92" cy="150" r="20"/>
      <circle class="disc" cx="290" cy="362" r="40"/>
      <circle class="disc" cx="402" cy="396" r="14"/>

      <g class="conference-title" text-anchor="middle">
        <text class="title-text" x="400" y="142" font-size="24">Frame, Signal,</text>
        <text class="title-text" x="400" y="168" font-size="24">and Score</text>
        <text class="title-text" x="400" y="194" font-size="24">Conference</text>
        <text class="detail-text" x="400" y="222" font-size="12.5">Call for Papers, Films</text>
        <text class="detail-text" x="400" y="238" font-size="12.5">and Exhibitors</text>
        <text class="detail-text" x="400" y="254" font-size="12.5">Now Open!</text>
        <text class="detail-text" x="400" y="276" font-size="7" letter-spacing="1">marrowgateindie.org</text>
      </g>

      <g class="event-place" text-anchor="middle">
        <text class="detail-text" x="232" y="188" font-size="7" letter-spacing="0.8">September 5–8, 2016</text>
        <text class="title-text" x="232" y="208" font-size="13">Marrowgate Shore</text>
        <text class="title-text" x="232" y="226" font-size="13">California</text>
      </g>

      <g class="paper-deadline" text-anchor="middle">
        <text class="title-text" x="598" y="228" font-size="14">Paper</text>
        <text class="title-text" x="598" y="246" font-size="14">Deadline</text>
        <text class="detail-text" x="598" y="264" font-size="8" letter-spacing="1">April 1, 2016</text>
      </g>
    </svg>
  </section>

</body>
</html>
```